Larkmoor 1852 Gin and Vodka labels

I am after a label for Gin and Vodka bottles.
I am crafting a gin and vodka for our property in Richmond, Tasmania which is called Larkmoor House (circa 1840) and is the old police magistrates home in Richmond complete with historic prison cells.
I would like to use a prison bar theme for the label. I have attempted a label myself which is attached. I would welcome the use and modification of this label or starting again using your own creative mind. This label was designed to go seamless on a black flask type bottle (200ml and 500ml) for Gin, but I will also need a label to go onto a clear bottle for the vodka, so this will need to be in black/silver grey (keeping it monotone please) print.
I would also like to include a label for the rear (or side) of the bottle as per the details on the attached word document.
The labels will be printed directly on the bottles so for the clear bottle we will most likely need a side label as otherwise with printing on the back and clear liquor this will ruin the effect of the label on the front.
I have also attached a picture of the black bottles that we are using for your reference. The clear bottles will be similar (see attached)

Target Market(s)

Gin and Vodka Drinkers

Colors

Designer to choose only greyscale colors for use in the design.

Requirements
Must have
• Use of the Larkmoor 1852 prison bar theme. one for gin, one for vodka, one for 500ml, one for 200ml
Nice to have
• Prison Bars

```html
<!DOCTYPE html>
<html lang="en">
<head>
<meta charset="utf-8">
<title>Larkmoor 1852 Gin and Vodka labels</title>
<link rel="stylesheet" href="https://fonts.googleapis.com/css2?family=Oswald:wght@600&family=Alfa+Slab+One&family=Tinos:wght@400;700&display=swap">
<style>
  :root {
    --backdrop: #e4e4e4;
    --label-black: #151515;
    --label-edge: #2a2a2a;
    --ink-white: #f2f2f2;
    --ink-grey: #bdbdbd;
    --bar-grey: #5a5a5a;
    --warning-red: #c8102e;
  }
  * { box-sizing: border-box; margin: 0; padding: 0; }
  html, body { width: 1200px; height: 818px; overflow: hidden; }
  body {
    background: var(--backdrop);
    display: flex;
    align-items: center;
    justify-content: center;
    gap: 40px;
    font-family: "Tinos", serif;
  }
  .label {
    position: relative;
    width: 340px;
    height: 300px;
    background: var(--label-black);
    border: 1px solid var(--label-edge);
    color: var(--ink-white);
    overflow: hidden;
  }
  /* brand name block */
  .brand-name {
    font-family: "Oswald", sans-serif;
    font-weight: 600;
    color: var(--ink-white);
    text-align: center;
    line-height: 0.95;
    text-transform: uppercase;
  }
  .brand-name span { display: block; }
  .brand-name .brand-year { font-size: 2.3em; letter-spacing: 0.02em; }

  /* rear label */
  .rear-label { text-align: center; font-size: 9px; letter-spacing: 0.08em; text-transform: uppercase; }
  .rear-label .brand-name { position: absolute; top: 16px; right: 14px; font-size: 10px; }
  .tasmania-outline {
    position: absolute; top: 28px; left: 128px;
    width: 70px; height: 58px;
    background: radial-gradient(ellipse at center, #3a3a3a 0%, #232323 80%);
    border-radius: 40% 45% 50% 40%;
  }
  .origin { position: absolute; top: 66px; left: 0; right: 0; font-size: 10px; color: var(--ink-grey); }
  .maker-block { position: absolute; top: 110px; left: 0; right: 0; }
  .maker-block p { color: var(--ink-grey); line-height: 1.35; }
  .maker-block .role { font-size: 10px; margin-top: 8px; }
  .maker-block .maker { font-weight: 700; font-size: 10.5px; color: var(--ink-white); }
  .web-pill {
    position: absolute; top: 224px; left: 60px; width: 220px; height: 22px;
    border: 1px solid var(--ink-grey); border-radius: 11px;
    display: flex; align-items: center; gap: 8px; padding-left: 4px;
    font-size: 8.5px; color: var(--ink-grey); text-transform: uppercase;
  }
  .web-pill svg { flex: none; }
  .pregnancy-warning {
    position: absolute; left: 12px; bottom: 12px; width: 104px; height: 28px;
    background: #fff; color: #111; display: flex; align-items: center; gap: 4px;
    padding: 2px 4px; text-transform: none; letter-spacing: 0; text-align: left; font-family: Arial, sans-serif;
  }
  .pregnancy-warning .mark { flex: none; width: 14px; height: 14px; border-radius: 50%; border: 2px solid var(--warning-red); }
  .pregnancy-warning b { display: block; color: var(--warning-red); font-size: 6.5px; }
  .pregnancy-warning span { font-size: 5.5px; line-height: 1.1; display: block; }
  .partner-badge { position: absolute; right: 12px; bottom: 12px; width: 24px; height: 28px; background: #3b3b3b; }

  /* front labels */
  .bars-scene {
    position: absolute; top: 0; left: 0; right: 0; height: 180px;
    background:
      linear-gradient(90deg, transparent 10%, #3c3c3c 12%, #262626 15%, transparent 17%,
                             transparent 83%, #3c3c3c 85%, #262626 88%, transparent 90%),
      radial-gradient(ellipse at 50% 55%, #2c2c2c 0%, var(--label-black) 75%);
  }
  .bars-scene::before, .bars-scene::after {
    content: ""; position: absolute; top: 84px; width: 44px; height: 46px; border-radius: 12px;
    background: linear-gradient(#d8d8d8, #9a9a9a);
  }
  .bars-scene::before { left: 64px; }
  .bars-scene::after { right: 64px; }
  .front-label .brand-name { position: absolute; top: 18px; left: 0; right: 0; font-size: 16px; }
  .spirit-name {
    position: absolute; top: 150px; left: 0; right: 0; text-align: center;
    font-family: "Alfa Slab One", serif; font-size: 56px; line-height: 1; color: var(--ink-white);
  }
  .story { position: absolute; top: 218px; left: 20px; right: 20px; text-align: center; line-height: 1.25; }
  .story .history { font-size: 9.5px; }
  .story .inspiration { font-size: 7.5px; color: var(--ink-grey); margin-top: 2px; }
  .standard-drinks { position: absolute; left: 16px; bottom: 14px; width: 22px; height: 26px; border: 1px solid var(--ink-grey); background: #2b2b2b; }
  .volume, .strength { position: absolute; bottom: 16px; font-weight: 700; font-size: 13px; }
  .volume { left: 130px; }
  .strength { right: 30px; }
</style>
</head>
<body>

  <section class="label rear-label" aria-label="Rear label">
    <div class="brand-name"><span>Larkmoor</span><span class="brand-year">1852</span><span>House</span></div>
    <div class="tasmania-outline" role="img" aria-label="Outline map of Tasmania"></div>
    <p class="origin">Product of Tasmania</p>
    <div class="maker-block">
      <p class="role">Distilled by</p>
      <p class="maker">Greystone Spirits Co.</p>
      <p>Using botanicals from Larkmoor House</p>
      <p class="role">Bottled by</p>
      <p class="maker">Harrow &amp; Kell</p>
      <p>In the servants quarters at Larkmoor House,<br>Richmond, Tasmania</p>
    </div>
    <div class="web-pill">
      <svg width="16" height="16" viewBox="0 0 16 16"><circle cx="8" cy="8" r="7.5" fill="#f2f2f2"/><circle cx="8" cy="8" r="4.5" fill="none" stroke="#151515" stroke-width="1"/><path d="M3.5 8h9M8 3.5v9" stroke="#151515" stroke-width="1"/></svg>
      larkmoorspirits.com.au
    </div>
    <div class="pregnancy-warning">
      <div class="mark"></div>
      <div><b>PREGNANCY WARNING</b><span>Alcohol can cause lifelong harm to your baby</span></div>
    </div>
    <div class="partner-badge"></div>
  </section>

  <section class="label front-label gin-label" aria-label="Gin front label">
    <div class="bars-scene" role="img" aria-label="Two fists gripping iron prison bars"></div>
    <div class="brand-name"><span>Larkmoor</span><span class="brand-year">1852</span><span>House</span></div>
    <h2 class="spirit-name">GIN</h2>
    <div class="story">
      <p class="history">Built circa 1840 and subsequently residence of Police Magistrate Major Edmund Tarrant</p>
      <p class="inspiration">Our gin is inspired by the convict heritage<br>of the home for which it is named after.</p>
    </div>
    <div class="standard-drinks"></div>
    <span class="volume">500ML</span>
    <span class="strength">45% ABV</span>
  </section>

  <section class="label front-label vodka-label" aria-label="Vodka front label">
    <div class="bars-scene" role="img" aria-label="Two fists gripping iron prison bars"></div>
    <div class="brand-name"><span>Larkmoor</span><span class="brand-year">1852</span><span>House</span></div>
    <h2 class="spirit-name">VODKA</h2>
    <div class="story">
      <p class="history">Built circa 1840 and subsequently residence of Police Magistrate Major Edmund Tarrant</p>
      <p class="inspiration">Our vodka is inspired by the convict heritage<br>of the home for which it is named after.</p>
    </div>
    <div class="standard-drinks"></div>
    <span class="volume">500ML</span>
    <span class="strength">45% ABV</span>
  </section>

</body>
</html>
```